Book Title: “Faith: Road of Endless Grace” Please see the attachment “Text on the cover”.

Book Cover Design Instructions: This book is meant for people of all religions and nationalities. Therefore, on the cover, there should be no mosque or an object specific to any religion. The primary emphasis should be on the "unconditional love of God." Therefore, use universal symbols of love. The second priority themes could be Sufism, Peace, and self-improvement. Rest is your imagination. Please also see the attachment: 'Book description and author's Bio.'
This book has the potential to be a best seller. Please do a good job.
What Book Cover Formats are required: A designer should submit cover designs in three formats: (1) eBook, (2) Paperback, and (3) Hardback. These books will be published on Borvex QPL.
Format requirements for eBooks are available from: https://qpl.borvex.example/en_US/help/topic/R731928457.
You can find paperback and hardback cover measurements from: https://qpl.borvex.example/en_US/cover-calculator
• To complete the project, all three formats should be accepted by Borvex QPL.
• The book interior trim size is 6.14 X 9.21 inches.
• Interior Type: Premium color.
• No bleed.
• I do not upload barcode. So, the back cover should have room for Borvex to print the barcode.
• Number of pages 126.
Compensation for the designer: After selecting one designer, I will increase the amount by $200 on Artvelle to compensate for three deliverables.
Follow-up of the Project:
After the book is published, I may need minor revisions. For example, the number of pages may change. Therefore, I will need the same design in revised sizes. In that case, I will pay $25 for each revision. For example, if the number of pages changes, I will need a different spine for paperback and hardback, then I will pay the artist $25 + $25 = $50 for both designs.
List of Enclosers:
1. Text on the cover.
2. Book description and author's Bio for the back cover.
3. Later, I will upload my picture for the book's back cover.

Target Market(s)

Any adult

Industry/Entity Type

Any industry

Requirements
Must have
• Three Deliverables

```html
<!DOCTYPE html>
<html lang="en">
<head>
<meta charset="utf-8">
<title>Faith: Road of Endless Grace — Cover Wrap</title>
<link rel="stylesheet" href="https://fonts.googleapis.com/css2?family=Abril+Fatface&family=Playfair+Display:wght@700;800;900&family=Montserrat:wght@400;500&family=Ubuntu:wght@700&display=swap">
<style>
  :root {
    --navy: #05135e;
    --navy-ink: #0b1660;
    --gold-dark: #d5b95c;
    --gold-pale: #e9e79d;
    --gold-text: #e3cf6a;
    --photo-box: #132a63;
    --white: #ffffff;
  }
  * { margin: 0; padding: 0; box-sizing: border-box; }
  html, body { width: 1200px; height: 847px; overflow: hidden; background: var(--navy); }
  .cover { position: relative; width: 1200px; height: 847px; background: var(--navy); overflow: hidden; }

  .band { position: absolute; left: 0; width: 1200px;
    background: linear-gradient(90deg, var(--gold-dark) 0%, var(--gold-pale) 40%, var(--gold-pale) 60%, var(--gold-dark) 100%); }
  .band--top { top: 34px; height: 127px; }
  .band--bottom { top: 767px; height: 80px; }

  .back-title { position: absolute; left: 0; width: 570px; top: 52px; text-align: center;
    font-family: "Playfair Display", serif; font-weight: 900; color: var(--navy-ink);
    font-size: 49px; line-height: 44px; letter-spacing: 1px; }

  .front-tagline { position: absolute; left: 690px; width: 455px; top: 73px; text-align: center;
    font-family: "Playfair Display", serif; font-weight: 800; color: var(--navy-ink);
    font-size: 21px; line-height: 31px; letter-spacing: 2.2px; }

  .back-tagline { position: absolute; left: 35px; width: 500px; top: 181px; text-align: center;
    font-family: "Playfair Display", serif; font-weight: 800; color: var(--white);
    font-size: 15px; line-height: 23px; letter-spacing: 1.6px; }

  .blurb { position: absolute; left: 35px; top: 236px; width: 495px;
    font-family: "Montserrat", sans-serif; font-size: 10.6px; line-height: 15.9px; color: var(--white); }
  .blurb p { text-align: justify; margin-bottom: 8.2px; }
  .blurb ol { list-style: none; margin-bottom: 8.2px; }
  .blurb li { text-align: left; }
  .blurb .num { display: inline-block; width: 22px; }

  .author-photo { position: absolute; left: 35px; top: 642px; width: 104px; height: 93px; background: var(--photo-box); }
  .author-name { position: absolute; left: 153px; top: 641px;
    font-family: "Ubuntu", sans-serif; font-weight: 700; font-size: 20px; color: var(--gold-text); }
  .author-bio { position: absolute; left: 154px; top: 667px; width: 378px;
    font-family: "Montserrat", sans-serif; font-size: 11.2px; line-height: 17.8px; color: var(--white); text-align: justify; }

  .front-author { position: absolute; left: 690px; width: 455px; top: 787px; text-align: right;
    font-family: "Playfair Display", serif; font-weight: 900; color: var(--navy-ink);
    font-size: 31px; letter-spacing: 7.5px; line-height: 40px; }

  .art { position: absolute; left: 0; top: 0; }
  .display { font-family: "Abril Fatface", serif; }
  .spine-name { font-family: "Playfair Display", serif; font-weight: 800; }
</style>
</head>
<body>
<main class="cover">
  <div class="band band--top"></div>
  <div class="band band--bottom"></div>

  <h2 class="back-title">FAITH: ROAD OF<br>ENDLESS GRACE</h2>
  <p class="front-tagline">GUIDE TO CULTIVATING<br>INNER PEACE AND MINDFUL LIVING</p>

  <section class="back-cover">
    <h3 class="back-tagline">GUIDE TO CULTIVATING<br>INNER PEACE AND MINDFUL LIVING</h3>
    <div class="blurb">
      <p>This book carefully weaves the gentle teachings of Sufism together with the timeless wisdom of sacred scripture to offer a complete roadmap for personal spiritual growth. The reader has a chance to experience firsthand the deep calm and boundless grace that seekers have treasured for centuries. This book addresses the following essential questions:</p>
      <ol>
        <li><span class="num">1.</span>How can one love the Divine without conditions? It is the highest of all forms of love and it sparks a deep and lasting inner journey.</li>
        <li><span class="num">2.</span>How to feel the love of the Divine, which can bring lasting calm and contentment.</li>
        <li><span class="num">3.</span>How to love yourself without conditions, which nurtures growth and inner harmony.</li>
        <li><span class="num">4.</span>What is the wisest way to meet life’s hardest moments so that pain eases and healing comes sooner?</li>
      </ol>
      <p>This book also explores the strong call to avoid oppression and injustice, a theme that sacred scripture returns to hundreds of times. Refusing to wrong others in every human encounter should be the first concern of every seeker.</p>
      <p>The sage Amaran did not only speak of peace and love. He showed a living example when he came to lead the city of Velmora without bloodshed. He did not gain power through birthright, and Velmora was home to many faiths. It stands as an early model of a wide and peaceful handover of power.</p>
      <p>Likewise, he agreed to the Accord of Tessaly with his fiercest rival, choosing a patient and peaceful path to end a long and bitter conflict that had cost many lives.</p>
      <p>The heart of this book is a clear method, in practical steps, for reaching a fully settled and contented soul (Nafs-e-Mutma’inna), the goal of every traveler on the Sufi path.</p>
    </div>
    <div class="author-photo" role="img" aria-label="Author portrait photo"></div>
    <h4 class="author-name">Dr. Ilyas Rahmani</h4>
    <p class="author-bio">Dr. Rahmani holds a Master’s in Chemistry and a Master’s in Data Science and worked as a Systems Analyst. He earned his Ph.D. in Comparative Religion. He helped found a community center in Northbrook.</p>
  </section>

  <svg class="art" width="1200" height="847" viewBox="0 0 1200 847" aria-label="Faith: Road of Endless Grace">
    <defs>
      <linearGradient id="goldFill" x1="0" y1="0" x2="0" y2="1">
        <stop offset="0" stop-color="#d2b150"/>
        <stop offset="0.45" stop-color="#e7e493"/>
        <stop offset="1" stop-color="#cdb155"/>
      </linearGradient>
      <linearGradient id="goldSpine" x1="0" y1="0" x2="1" y2="0">
        <stop offset="0" stop-color="#d2b150"/>
        <stop offset="0.5" stop-color="#e7e493"/>
        <stop offset="1" stop-color="#cdb155"/>
      </linearGradient>
    </defs>

    <g class="spine-title display" fill="url(#goldSpine)" transform="translate(630,213) rotate(90)">
      <text x="0" y="26" font-size="31" textLength="100" lengthAdjust="spacingAndGlyphs">FAITH:</text>
      <text x="0" y="55" font-size="31" textLength="82" lengthAdjust="spacingAndGlyphs">ROAD</text>
      <line x1="122" y1="29" x2="145" y2="29" stroke="#ffffff" stroke-width="1.2"/>
      <text x="158" y="35" font-size="17" fill="#ffffff" text-anchor="middle">of</text>
      <line x1="171" y1="29" x2="195" y2="29" stroke="#ffffff" stroke-width="1.2"/>
      <text x="205" y="26" font-size="31" textLength="118" lengthAdjust="spacingAndGlyphs">ENDLESS</text>
      <text x="226" y="55" font-size="31" textLength="82" lengthAdjust="spacingAndGlyphs">GRACE</text>
    </g>
    <g class="spine-author spine-name" fill="#ffffff" transform="translate(630,213) rotate(90)">
      <text x="362" y="27" font-size="17" textLength="141" lengthAdjust="spacing">DR. ILYAS</text>
      <text x="391" y="45" font-size="17" textLength="83" lengthAdjust="spacing">RAHMANI</text>
    </g>

    <g class="front-title display" fill="url(#goldFill)">
      <text x="688" y="315" font-size="132" textLength="460" lengthAdjust="spacingAndGlyphs">FAITH:</text>
      <text x="750" y="431" font-size="132" textLength="343" lengthAdjust="spacingAndGlyphs">ROAD</text>
      <text x="670" y="596" font-size="110" textLength="495" lengthAdjust="spacingAndGlyphs">ENDLESS</text>
      <text x="748" y="708" font-size="125" textLength="339" lengthAdjust="spacingAndGlyphs">GRACE</text>
    </g>
    <g class="front-of">
      <path d="M748 474 L882 472 L882 477 Z" fill="#ffffff"/>
      <path d="M955 472 L1089 474 L955 477 Z" fill="#ffffff"/>
      <text class="display" x="918" y="493" font-size="54" fill="#ffffff" text-anchor="middle">of</text>
    </g>
  </svg>

  <p class="front-author">DR. ILYAS RAHMANI</p>
</main>
</body>
</html>
```